Laser Tattoo Removal Business Cards

We are looking for a professional business card design for a laser tattoo removal business. Ideally looking for a black business card design. The name of the business is Brightline Tattoo Removal. We place our cards at local tattoo shops so we ideally are looking for something trendy/edgy to draw both male and female clientele in.

Target Market(s)

Male/Female ages 18-60

Contact Information for Business Card

black background ideally.. hoping to stay within greys, whites and black

Font styles to use
Serif
Sans Serif

Colors
121212
a9a9a9
5c5c5c
f5f5f5
ffffff
7f7f7f
606060
848484
9d9d9d

Requirements
Must have
• Employee Info:
• Melissa Thornbury
• Chief Executive Offer
• m: 919.537.2846
• w: 919.362.4178
• f: 919.685.3907
• mthornbury@brightlinetattooremoval.example
• Address:
• 4615 Oakmere Pkwy, Suite 210
• Raleigh, NC 27654
• Website:
• www.brightlinetattooremoval.example
Nice to have
• Myabe business name on back or logo on back and employee info on the front

```html
<!DOCTYPE html>
<html lang="en">
<head>
<meta charset="utf-8">
<title>Brightline Tattoo Removal — Business Cards</title>
<link rel="stylesheet" href="https://fonts.googleapis.com/css2?family=Josefin+Sans:wght@400;600&family=Roboto+Condensed:wght@400;700&family=Roboto:wght@300;400&display=swap">
<style>
  :root {
    --stage: #2b2825;
    --card: #121212;
    --white: #ffffff;
    --soft: #f5f5f5;
    --grey: #a9a9a9;
    --rule: #f5f5f5;
  }
  * { margin: 0; padding: 0; box-sizing: border-box; }
  html, body { width: 1200px; height: 769px; overflow: hidden; background: var(--stage); }
  .canvas { position: relative; width: 1200px; height: 769px; }

  .card {
    position: absolute;
    width: 520px; height: 297px;
    background: var(--card);
    border-radius: 3px;
    color: var(--white);
    font-family: "Roboto", sans-serif;
    overflow: hidden;
  }
  .card--front { left: 50px; top: 236px; }
  .card--back { left: 630px; top: 236px; }

  .wordmark { position: absolute; text-align: center; }
  .wordmark__name {
    font-family: "Josefin Sans", sans-serif;
    font-weight: 600;
    font-size: 34px;
    letter-spacing: 3px;
    color: var(--white);
    line-height: 1;
  }
  .wordmark__tagline {
    display: flex; align-items: center; justify-content: center; gap: 8px;
    margin-top: 12px;
    font-family: "Josefin Sans", sans-serif;
    font-weight: 600;
    font-size: 13px;
    letter-spacing: 3px;
    color: var(--white);
  }
  .wordmark__tagline::before, .wordmark__tagline::after {
    content: ""; width: 18px; height: 1px; background: var(--soft);
  }
  .card--front .wordmark { left: 30px; top: 46px; width: 240px; }
  .card--back .wordmark { left: 0; right: 0; top: 92px; }
  .card--back .wordmark__name { font-size: 40px; }

  .website-back {
    position: absolute; left: 0; right: 0; top: 210px;
    text-align: center;
    font-size: 12px; letter-spacing: 2.5px; color: var(--soft);
  }

  .person { position: absolute; right: 40px; top: 38px; text-align: right; }
  .person__name {
    font-family: "Roboto Condensed", sans-serif; font-weight: 700;
    font-size: 18px; letter-spacing: 0.5px; line-height: 1.1;
  }
  .person__title { font-size: 12px; color: var(--soft); }
  .person-marker {
    position: absolute; right: 14px; top: 34px;
    width: 14px; height: 26px; background: var(--white);
  }

  .rule { position: absolute; height: 1px; background: var(--rule); }
  .rule--main { left: 150px; right: 30px; top: 128px; }
  .rule--contact { left: 30px; width: 150px; top: 196px; }

  .address {
    position: absolute; right: 40px; top: 138px;
    text-align: right; font-size: 12.5px; line-height: 1.4; color: var(--soft);
    font-weight: 300;
  }

  .contacts { position: absolute; left: 30px; top: 206px; list-style: none; }
  .contacts__item {
    display: flex; align-items: center; gap: 8px;
    font-size: 12.5px; line-height: 1.45; color: var(--soft); font-weight: 300;
  }
  .contacts__icon { width: 11px; height: 11px; flex: none; fill: var(--white); }
</style>
</head>
<body>
<main class="canvas">

  <section class="card card--front" aria-label="Business card front">
    <div class="wordmark">
      <div class="wordmark__name">BRIGHTLINE</div>
      <div class="wordmark__tagline">TATTOO REMOVAL</div>
    </div>

    <div class="person-marker"></div>
    <div class="person">
      <div class="person__name">MELISSA THORNBURY</div>
      <div class="person__title">Chief Executive Offer</div>
    </div>

    <div class="rule rule--main"></div>

    <div class="address">
      4615 Oakmere Pkwy<br>
      Suite 210<br>
      Raleigh, NC 27654<br>
      www.brightlinetattooremoval.example
    </div>

    <div class="rule rule--contact"></div>
    <ul class="contacts">
      <li class="contacts__item">
        <svg class="contacts__icon" viewBox="0 0 12 12" aria-hidden="true"><path d="M2.5 1l2 2.2-1.2 1.3c.7 1.6 2 2.9 3.6 3.6L8.2 7l2.3 2-1.2 1.8C5 10.5 1.5 7 1.2 2.6z"/></svg>
        919.362.4178
      </li>
      <li class="contacts__item">
        <svg class="contacts__icon" viewBox="0 0 12 12" aria-hidden="true"><path d="M3 0h6v12H3zM4 1.5v8h4v-8z"/></svg>
        919.537.2846
      </li>
      <li class="contacts__item">
        <svg class="contacts__icon" viewBox="0 0 12 12" aria-hidden="true"><path d="M3 0h6v3H3zM0 4h12v6h-2V8H2v2H0zM2.5 9h7v3h-7z"/></svg>
        919.685.3907
      </li>
      <li class="contacts__item">
        <svg class="contacts__icon" viewBox="0 0 12 12" aria-hidden="true"><path d="M0 2h12v8H0zM1 3l5 3.5L11 3z" fill-rule="evenodd"/></svg>
        mthornbury@brightlinetattooremoval.example
      </li>
    </ul>
  </section>

  <section class="card card--back" aria-label="Business card back">
    <div class="wordmark">
      <div class="wordmark__name">BRIGHTLINE</div>
      <div class="wordmark__tagline">TATTOO REMOVAL</div>
    </div>
    <div class="website-back">www.brightlinetattooremoval.example</div>
  </section>

</main>
</body>
</html>
```